Counseling Practice Business Card

I need a professional looking business card incorporating my new logo that was just completed. Card needs to incorporate my name and title, description of my specialty, my address, my phone number, my fax number, my email and my website URL. I need to be able to choose design on/with different paper colors and textures.
I do not have a lot of business card ideas so I am open to anything but I want bold,sharp, clear card without additional designs other than my logo (see attached file info). I am open to different color backgrounds or paper colors including black. I do not like traditional brackets around area codes in phone number or dashes between numbers in phone number. Am open to other ways of presenting including periods between numbers as appropriate. I do not know enough to know what I like yet but I want card to coordinate and work together with my logo. My practice emphasizes natural mental health interventions so any use of color (with background paper color or the blue and green in my logo) that elicits nature is nice. In addition to black, any natural brown or wood looking background might be desirable also. Most of the offerings so far look very similar and boring.

Target Market(s)

Potential therapy clients and other professionals

Contact Information for Business Card

Card information:
Gerald M. Whitcombe, Ph.D.
Licensed Clinical Psychologist
Integrative Health Coach
4812 Marlowe Ridge Blvd SE
Suite 310
Duluth, GA 30096
770.415.2983 phone
770.581.4096 fax
drgeraldwhitcombe@quillmarsh.net
brightfernwellness.net

Font styles to use
Serif
Sans Serif
Other font styles liked:
• anything that you think looks crisp, clear and easily readable

Requirements
Must have
• Any color used should coordinate with my logo design (see attached files).
• Card should be printed horizontally so top and bottom are longest sides of rectangle.
• Background color or paper color should complement and highlight logo. Do not like a white background. black, grey, brown or any color my logo would blend well with.
Nice to have
• I would like designer to utilize color to highlight letters/name or phone-fax-web symbols.
• Bottom edge of card could be highlighted if appropriate to an idea.
Should not have
• I would NOT want the card to have a pure white background at all.
• No clear cards.
• Cards should be oriented with long sides on bottom and top, NOT sides. DO NOT LIKE THIS THIN TALL ORIENTATION.

```html
<!DOCTYPE html>
<html lang="en">
<head>
<meta charset="utf-8">
<title>Brightfern Wellness – Business Card</title>
<link href="https://fonts.googleapis.com/css2?family=Jost:wght@400;500;600&display=swap" rel="stylesheet">
<style>
  :root{
    --stage:#1c1c1e;
    --navy:#18203a;
    --navy-light:#2a3658;
    --paper:#f1f2f4;
    --blue:#1f73c6;
    --ink:#4a4d52;
    --ink-dark:#2e3035;
    --white:#ffffff;
  }
  *{box-sizing:border-box;margin:0;padding:0}
  html,body{width:1200px;height:913px;overflow:hidden;background:var(--stage)}
  body{font-family:"Jost",Arial,sans-serif;position:relative}
  .card{position:absolute;left:290px;width:620px;height:354px;border-radius:4px;overflow:hidden;box-shadow:0 10px 30px rgba(0,0,0,.5)}
  .card--front{top:70px;background:var(--navy)}
  .card--back{top:489px;background:var(--paper)}
  .front-pattern{position:absolute;inset:0;background:radial-gradient(ellipse at 50% 45%,var(--navy-light),var(--navy) 75%)}
  .brand{position:absolute;left:0;right:0;text-align:center;font-weight:600;letter-spacing:.5px;white-space:nowrap}
  .card--front .brand{top:142px;font-size:52px;color:var(--white);line-height:1}
  .card--back .brand{top:32px;font-size:32px;color:var(--blue);line-height:1}
  .identity{position:absolute;top:86px;left:0;right:0;text-align:center}
  .identity__name{font-size:24px;font-weight:600;color:var(--blue)}
  .identity__title{font-size:15px;color:var(--ink);margin-top:2px}
  .identity__specialty{font-size:18px;color:var(--ink)}
  .divider{position:absolute;left:36px;right:36px;top:194px;height:2px;background:var(--blue)}
  .address{position:absolute;right:40px;top:210px;text-align:right;font-size:15px;font-weight:600;font-style:normal;color:var(--ink-dark);line-height:1.35}
  .contacts{position:absolute;left:40px;top:222px;list-style:none;font-size:15px;color:var(--ink);line-height:1.55}
  .contacts li{display:flex;align-items:center;gap:10px;white-space:nowrap}
  .contacts svg{width:15px;height:15px;flex:none;fill:var(--blue)}
</style>
</head>
<body>
  <section class="card card--front" aria-label="Card front">
    <div class="front-pattern" role="img" aria-label="Fine navy geometric floral pattern filling the card face"></div>
    <div class="brand">Brightfern Wellness</div>
  </section>

  <section class="card card--back" aria-label="Card back">
    <div class="brand">Brightfern Wellness</div>
    <div class="identity">
      <div class="identity__name">Gerald M. Whitcombe, Ph.D.</div>
      <div class="identity__title">Licensed Clinical Psychologist</div>
      <div class="identity__specialty">Integrative Health Coach</div>
    </div>
    <div class="divider"></div>
    <address class="address">
      4812 Marlowe Ridge Blvd SE<br>Suite 310<br>Duluth, GA 30096
    </address>
    <ul class="contacts">
      <li><svg viewBox="0 0 24 24" aria-hidden="true"><path d="M6.6 10.8a15 15 0 0 0 6.6 6.6l2.2-2.2a1 1 0 0 1 1-.25 11.4 11.4 0 0 0 3.6.57 1 1 0 0 1 1 1V20a1 1 0 0 1-1 1A17 17 0 0 1 3 4a1 1 0 0 1 1-1h3.5a1 1 0 0 1 1 1c0 1.25.2 2.45.57 3.57a1 1 0 0 1-.25 1z"/></svg>770.415.2983</li>
      <li><svg viewBox="0 0 24 24" aria-hidden="true"><path d="M6 2h9l3 3v5H6zM3 10h18v10H3zm3 3v2h2v-2zm4 0v2h2v-2zm4 0v2h4v-2zm-8 4v1h12v-1z"/></svg>770.581.4096</li>
      <li><svg viewBox="0 0 24 24" aria-hidden="true"><path d="M12 2a10 10 0 1 0 5 18.7l-1-1.7A8 8 0 1 1 20 12v1a2 2 0 0 1-4 0V7h-2v1a5 5 0 1 0 .9 7.2A4 4 0 0 0 22 13v-1A10 10 0 0 0 12 2zm0 13a3 3 0 1 1 0-6 3 3 0 0 1 0 6z"/></svg>drgeraldwhitcombe@quillmarsh.net</li>
      <li><svg viewBox="0 0 24 24" aria-hidden="true"><path d="M12 2a10 10 0 1 0 0 20 10 10 0 0 0 0-20zm6.9 6h-3a15 15 0 0 0-1.3-3.9A8 8 0 0 1 18.9 8zM12 4a13 13 0 0 1 1.9 4h-3.8A13 13 0 0 1 12 4zM4.3 14a8 8 0 0 1 0-4h3.4a16 16 0 0 0 0 4zm.8 2h3a15 15 0 0 0 1.3 3.9A8 8 0 0 1 5.1 16zm3-8h-3a8 8 0 0 1 4.3-3.9A15 15 0 0 0 8.1 8zM12 20a13 13 0 0 1-1.9-4h3.8A13 13 0 0 1 12 20zm2.3-6H9.7a14 14 0 0 1 0-4h4.6a14 14 0 0 1 0 4zm.3 5.9a15 15 0 0 0 1.3-3.9h3a8 8 0 0 1-4.3 3.9zm1.7-5.9a16 16 0 0 0 0-4h3.4a8 8 0 0 1 0 4z"/></svg>brightfernwellness.net</li>
    </ul>
  </section>
</body>
</html>
```